Broschüren-Design für Bauunternehmen
Zielgruppe
Wir bauen Neubauten in Massiv Bauweise, als Bauträger und Generalunternehmer in Raum Baden-Baden und Umgebung. Zielgruppe sind alle Altersgruppen, jedoch möchten wir gerade junge Familien mit Kindern unterstützen ihr e induvidueles Traumhaus mit Festpreis Garantien kostenbewusst zu ermöglichen.
Aufgabenstellung
Es sollte eine Image Broschüre Größe A4 in 12 Seiten ergeben. Unter Berücksichtigung dass es ein Imagespiegelung unseres website
design sollte.
Die Textinhalte sollten aus der Webseite übernommen werden und dürfen auch passend gekürzt werden.
Logo, Bilder welches in der Webseite ersichtlich sind sollten verwendet werden. Es können jedoch stock-bilder, Vektor Dateien bei bedarf verwendet werden. Diese werden dann dazu gekauft.
Inhalt:
Seite 1 - Startbild, Logo und Überschrift „Fest-gefügt - Rundum aus einem Guss - Vorlind Bauunternehmung aus Baden-Baden!'
Seite 2 - Philosophie, Bild Geschäftsführer; (Text siehe Startseite unter „Wir sind als Bauträger..........Wir beraten Sie gerne!')
Seite 3 - Über Uns, Bild Beratung (Text siehe über uns)
Seite 4 / 5 - Rundum Sicherheitspaket, Bilder Hand und Familie und Garantie Siegel (Text Leistungen/Sicherheitspaket)
Seite 6/7 - Bauberatung Bilder siehe Webseite
Seite 8 - Massivbau und Monolithische Bauweise ( Text Bauwissen/Massivbau und Bauwissen/Monolithische Bauweise) Wichtig Text passend kürzen.....
Seite 9 - Wohnraumlüftung - Bild siehe Webseite (Text Bauwissen/Raumklima)
Seite 10/11 - Finanzierung und BRT-Standards (Text Bauwissen)
Seite 12 - Kontakt und Adresse
Wie gesagt Designfarbe wie Webseite und logo. Längere Texte können zweispaltig geschrieben werden. Texte können gekürzt werden.
Bild Herkünfte siehe Impressum. können bei stock als Entwurf heruntergeladen werden. bei Finnisch werden sie nachgereicht.

```html
<!DOCTYPE html>
<html lang="de">
<head>
<meta charset="utf-8">
<title>Vorlind Bauunternehmung – Imagebroschüre</title>
<link href="https://fonts.googleapis.com/css2?family=Open+Sans:wght@300;400;600;700&display=swap" rel="stylesheet">
<style>
:root{
  --gold:#e3ad23;
  --gold-dark:#c8951a;
  --ink:#4a4a4a;
  --ink-soft:#6b6b6b;
  --paper:#ffffff;
  --panel:#ebebe9;
  --stage-light:#e8e8ec;
  --stage-dark:#3a3d38;
  --tick:#7cb63f;
}
*{box-sizing:border-box;margin:0;padding:0}
html,body{width:1200px;height:2400px;overflow:hidden}
body{font-family:'Open Sans',Arial,sans-serif;color:var(--ink);background:var(--stage-dark);position:relative}
.nowrap{white-space:nowrap}
.intro-stage{position:absolute;left:0;top:0;width:1200px;height:636px;background:var(--stage-light)}
.cover{position:absolute;left:84px;top:75px;width:332px;height:475px;background:var(--paper);box-shadow:0 6px 18px rgba(0,0,0,.18)}
.cover-brand{position:absolute;top:42px;left:0;width:100%;text-align:center;font-size:17px;font-weight:600;color:var(--ink)}
.cover-brand .dot{display:inline-block;width:10px;height:10px;background:var(--gold);border-radius:50%;margin-right:7px;vertical-align:middle}
.cover-photo{position:absolute;left:26px;top:112px;width:306px;height:250px;background:linear-gradient(170deg,#b9d3ea 0%,#e6ecef 45%,#c9ccc6 70%,#8f8d83 100%);clip-path:polygon(40px 0,100% 0,100% 100%,40px 100%,0 210px,0 40px)}
.cover-title{position:absolute;left:20px;right:20px;top:405px;text-align:center;color:var(--gold);font-size:11.5px;font-weight:600;line-height:1.35}

.label{position:absolute;left:158px;width:0;height:0}
.label span{position:absolute;left:0;top:0;transform:translate(-50%,-50%) rotate(-90deg);white-space:nowrap;color:#fff;font-size:30px;font-weight:400}

.spread{position:absolute;left:191px;width:757px;height:535px;background:var(--paper);overflow:hidden}
.spread.spread-mini{left:468px;top:75px;transform:scale(.872);transform-origin:0 0;box-shadow:0 6px 18px rgba(0,0,0,.18)}
.s-about{top:676px}
.s-safety{top:1230px}
.s-advice{top:1782px}
.abs{position:absolute}

/* about */
.quote-box{left:19px;top:18px;width:342px;height:499px;background:var(--gold);color:#fff}
.quote-mark{position:absolute;left:-2px;top:44px;font-size:130px;font-weight:700;line-height:1;font-family:Georgia,serif;letter-spacing:-14px}
.quote-text{position:absolute;left:80px;top:66px;width:244px;font-size:15.6px;font-weight:300;line-height:1.2}
.ceo-photo{left:80px;top:264px;width:73px;height:127px;background:linear-gradient(180deg,#d8dde2 0%,#b7a397 40%,#2d2f36 75%,#1d1f24 100%)}
.signature{left:80px;top:402px;width:60px;height:26px;background:rgba(255,255,255,.25)}
.ceo-name{left:80px;top:432px;font-size:7.5px}
.quote-side{left:184px;top:264px;width:144px;font-size:7.2px;line-height:1.6}
.quote-side strong{display:block;margin-top:8px;font-weight:600}
.consult-photo{left:420px;top:19px;width:337px;height:169px;background:linear-gradient(120deg,#e9e4dd 0%,#d2b899 40%,#8d8a8d 70%,#e0d6c4 100%);clip-path:polygon(0 0,100% 0,100% 100%,78px 100%)}
.h-gold{color:var(--gold);font-weight:400}
.about-title{left:430px;top:232px;font-size:16px}
.about-lead{left:430px;top:258px;width:290px;font-size:7.6px;line-height:1.45;color:var(--ink)}
.col{font-size:5.8px;line-height:1.45;color:var(--ink-soft)}
.col p{margin-bottom:6px}
.about-c1{left:430px;top:314px;width:135px}
.about-c2{left:575px;top:314px;width:140px}
.folio{font-size:5.8px;color:#999;bottom:16px}
.folio b{color:var(--gold);font-weight:600}

/* safety */
.family-photo{left:0;top:23px;width:378px;height:258px;background:linear-gradient(160deg,#f2f1ef 0%,#dcdad6 40%,#8ab0d0 70%,#e0e0de 100%)}
.safety-panel{left:378px;top:23px;width:379px;height:512px;background:var(--panel);clip-path:polygon(0 0,346px 0,100% 33px,100% 100%,0 100%)}
.safety-title{left:50px;top:314px;font-size:16px;line-height:1.2}
.safety-text{left:50px;top:370px;width:160px;font-size:7.6px;line-height:1.45}
.safety-text p{margin-bottom:8px}
.seal{left:228px;top:382px}
.feat-col{top:44px;width:160px}
.feat-col.c1{left:420px}
.feat-col.c2{left:582px}
.feat{position:relative;padding-left:14px;margin-bottom:10px;font-size:5.3px;line-height:1.42;color:var(--ink-soft)}
.feat h4{font-size:5.4px;font-weight:700;color:var(--ink)}
.feat svg{position:absolute;left:0;top:0}

/* advice */
.plan-photo{left:0;top:23px;width:378px;height:288px;background:linear-gradient(135deg,#f4f4f2 0%,#e2e0dc 45%,#d7c9c2 70%,#c9c7c3 100%);clip-path:polygon(0 0,100% 0,100% 245px,335px 100%,0 100%)}
.advice-title{left:50px;top:355px;font-size:15.5px;line-height:1.22}
.advice-text{left:50px;top:403px;width:258px;font-size:7.2px;line-height:1.45}
.step{left:420px;width:320px}
.step .icon{position:absolute;left:0;top:0}
.step h3{margin-left:64px;font-size:10.2px;line-height:1.2;font-weight:400;color:var(--gold)}
.step .txt{margin-left:64px;margin-top:6px;font-size:5.6px;line-height:1.5;color:var(--ink-soft)}
.step .txt p{margin-bottom:6px}
</style>
</head>
<body>

<section class="intro-stage">
  <div class="cover">
    <div class="cover-brand"><span class="dot"></span>Vorlind BauFest</div>
    <div class="cover-photo" role="img" aria-label="Foto: modernes weißes Einfamilienhaus mit Holzfassade unter blauem Himmel"></div>
    <p class="cover-title">Fest-gefügt – Rundum aus einem Guss –<br>Vorlind Bauunternehmung aus Baden-Baden!</p>
  </div>

  <div class="spread spread-mini">
    <div class="abs quote-box">
      <div class="quote-mark">„</div>
      <p class="quote-text">Wir sind als Bauträger und Generalunternehmer in <span class="nowrap">Baden-Baden</span> Ihr kompetenter Ansprechpartner für die Region. Ihr Wunschhaus bauen wir schlüsselfertig oder mit Baueigenleistungen ganz nach Ihrem Geschmack.</p>
      <div class="abs ceo-photo" role="img" aria-label="Porträtfoto des Geschäftsführers"></div>
      <div class="abs signature" role="img" aria-label="Unterschrift"></div>
      <p class="abs ceo-name">R. Vorlind</p>
      <p class="abs quote-side">Der solide Bau hat an Beliebtheit nie verloren. Warum? Ganz einfach: Weil der solide Bau Stein auf Stein ein Haus hochwertig und haltbar zugleich macht. Wir stehen für die grundsolide monolithische Ausführung unserer Projekte und verbinden modernes Bauen mit traditionsreichem Bauhandwerk. Ein schneller Baubeginn und Sorgfalt bei jeder Tätigkeit bringen Sie Ihrem Traumhaus im Massivbau Schritt für Schritt näher.<strong>Sprechen Sie uns an.<br>Wir beraten Sie gerne!</strong></p>
    </div>
    <div class="abs consult-photo" role="img" aria-label="Foto: Beratungsgespräch mit jungem Paar"></div>
    <h2 class="abs h-gold about-title">Über uns</h2>
    <p class="abs about-lead">Die Firma Vorlind Bauunternehmung als seriöser Anbieter von Dienstleistungen rund um den Hausbau steht für eine schnelle Umsetzung eines Hausbauprojekts, angefangen von der individuellen Planung bis hin zum abgeschlossenen Bau eines Hauses.</p>
    <p class="abs folio" style="right:20px">Über uns / <b>3</b></p>
  </div>
</section>

<div class="label" style="top:943px"><span>Über uns</span></div>
<div class="label" style="top:1497px"><span>Sicherheitspaket</span></div>
<div class="label" style="top:2050px"><span>Bauberatung</span></div>

<!-- Über uns -->
<section class="spread s-about">
  <div class="abs quote-box">
    <div class="quote-mark">„</div>
    <p class="quote-text">Wir sind als Bauträger und Generalunternehmer in <span class="nowrap">Baden-Baden</span> Ihr kompetenter Ansprechpartner für die Region. Ihr Wunschhaus bauen wir schlüsselfertig oder mit Baueigenleistungen ganz nach Ihrem Geschmack.</p>
    <div class="abs ceo-photo" role="img" aria-label="Porträtfoto des Geschäftsführers"></div>
    <div class="abs signature" role="img" aria-label="Unterschrift"></div>
    <p class="abs ceo-name">R. Vorlind</p>
    <p class="abs quote-side">Der solide Bau hat an Beliebtheit nie verloren. Warum? Ganz einfach: Weil der solide Bau Stein auf Stein ein Haus hochwertig und haltbar zugleich macht. Wir stehen für die grundsolide monolithische Ausführung unserer Projekte und verbinden modernes Bauen mit traditionsreichem Bauhandwerk. Ein schneller Baubeginn und Sorgfalt bei jeder Tätigkeit bringen Sie Ihrem Traumhaus im Massivbau Schritt für Schritt näher.<strong>Sprechen Sie uns an.<br>Wir beraten Sie gerne!</strong></p>
  </div>
  <div class="abs consult-photo" role="img" aria-label="Foto: Beratungsgespräch mit jungem Paar"></div>
  <h2 class="abs h-gold about-title">Über uns</h2>
  <p class="abs about-lead">Die Firma Vorlind Bauunternehmung als seriöser Anbieter von Dienstleistungen rund um den Hausbau steht für eine schnelle Umsetzung eines Hausbauprojekts, angefangen von der individuellen Planung bis hin zum abgeschlossenen Bau eines Hauses.</p>
  <div class="abs col about-c1">
    <p>Wir erfüllen Ihnen Ihren individuellen Traum vom Eigenheim und pflegen dazu Kontakte zu Partnern der entsprechenden Gewerke und auch zu Architekten, die Ihren individuellen Entwurf vom Traumhaus begleiten. Auch Baueigenleistungen Ihrerseits sind hierbei möglich.</p>
    <p>Unser oberstes Ziel ist es, Ihnen das Haus zu bauen oder bauen zu lassen, das zu Ihnen passt, ob es ein Massivbau Stein auf Stein, ein Einfamilienhaus als Doppel- oder Reihenhaus oder auch ein Energiesparhaus, gebaut nach den aktuellen Standards der Energieeffizienz BRT, ist, wir finden in einem persönlichen Gespräch das Richtige für Sie!</p>
    <p>Wir verfolgen die Philosophie der grundsoliden Qualität und legen dennoch besonderen</p>
  </div>
  <div class="abs col about-c2">
    <p>Wert auf eine schnelle Umsetzung. Zur Firmenphilosophie gehören ebenfalls eine geradlinige Vorgehensweise, die Garantie für einen fairen Festpreis und die Umsetzung neuester im Baugewerbe gültigen Standards.</p>
    <p>Die Firma Vorlind Bauunternehmung versteht sich als Ihr regionaler Ansprechpartner in Sachen schnelle Umsetzung eines Bauprojekts, legt Wert auf individuelle Beratung sowie absolute Zuverlässigkeit und Seriosität in Baden-Baden und angrenzender Umgebung.</p>
    <p>Unser Büro befindet sich im Lindenweg 7 in Baden-Baden und ist somit zentral gelegen (in der Fußgängerzone) und sehr gut zu erreichen. Sie sind uns sehr willkommen mit Ihrer Anfrage auf ein individuelles Bauprojekt, wir kümmern uns um die schnelle Umsetzung!</p>
  </div>
  <p class="abs folio" style="right:20px">Über uns / <b>3</b></p>
</section>

<!-- Sicherheitspaket -->
<section class="spread s-safety">
  <div class="abs family-photo" role="img" aria-label="Foto: junge Familie mit Kind unter einem Papierdach vor weißer Ziegelwand"></div>
  <h2 class="abs h-gold safety-title">Planung und finanzielle<br>Absicherung</h2>
  <div class="abs safety-text">
    <p>Die Vorlind Bauunternehmung legt größten Wert auf die Sicherheit der Bauausführung sowie deren Qualität, eine zuverlässige Planung und die finanzielle Absicherung unserer Kunden.</p>
    <p>Ein wichtiger Teilbereich ist die Planung und finanzielle Absicherung Ihres Bauvorhabens. Diese stellen wir durch folgende Leistungen und Maßnahmen sicher.</p>
  </div>
  <svg class="abs seal" width="104" height="104" viewBox="0 0 104 104" role="img" aria-label="Garantiesiegel">
    <circle cx="52" cy="52" r="50" fill="#7cb63f"/>
    <circle cx="52" cy="52" r="40" fill="#ffffff"/>
    <circle cx="52" cy="52" r="34" fill="none" stroke="#4a4a4a" stroke-width="1.5"/>
  </svg>

  <div class="abs safety-panel"></div>
  <div class="abs feat-col c1">
    <div class="feat"><svg width="10" height="9" viewBox="0 0 10 9"><path d="M1 5l3 3 5-7" fill="none" stroke="#7cb63f" stroke-width="2"/></svg><h4>Mit Festpreisgarantie bauen</h4>Als Bauherr benötigen Sie finanzielle Sicherheit beim Bau Ihres Eigenheims. Wir garantieren Ihnen den mit Vertragsabschluss vereinbarten Preis für die nächsten zwölf Monate. Unsere Garantie gibt Ihnen für jeden Eigenheimbesitzer unverzichtbare finanzielle Sicherheit.</div>
    <div class="feat"><svg width="10" height="9" viewBox="0 0 10 9"><path d="M1 5l3 3 5-7" fill="none" stroke="#7cb63f" stroke-width="2"/></svg><h4>Baufertigstellungs-Bürgschaft</h4>Unsere Baufertigstellungs-Bürgschaft gibt Ihnen zuverlässige Sicherheit. Auf Wunsch sichern wir alle Bauleistungen bis zur vereinbarten Höhe über eine Bürgschaft ab. Damit schützen wir Sie in jeder Situation vor bösen Überraschungen.</div>
    <div class="feat"><svg width="10" height="9" viewBox="0 0 10 9"><path d="M1 5l3 3 5-7" fill="none" stroke="#7cb63f" stroke-width="2"/></svg><h4>Baugrundgutachten durch geol. Institut</h4>Noch vor Baubeginn benötigen Sie alle relevanten Informationen über die Bodenbeschaffenheit Ihres Grundstücks. Denn auf Basis dieser Werte erfolgt die statische Berechnung für Ihr zukünftiges Zuhause. Diese Daten sind ein Teil der Garantie für die Sicherheit des Gebäudes und dessen Qualität. Wir arbeiten mit einem renommierten geologischen Institut zusammen, das für Sie diese Baugrundgutachten kostengünstig erstellt.</div>
    <div class="feat"><svg width="10" height="9" viewBox="0 0 10 9"><path d="M1 5l3 3 5-7" fill="none" stroke="#7cb63f" stroke-width="2"/></svg><h4>Unabhängiger Wirtschaftsprüfer verwaltet Baukonto</h4>Ihr Geld verwaltet ein unabhängiger Wirtschaftsprüfer. Alle durch Sie geleisteten Investitionen liegen auf einem eigenen Baukonto. Diese Maßnahme ist für Sie die Garantie, dass Ihr für den Massivbau eingeplantes Geld ausschließlich für den von Ihnen bestimmten Zweck eingesetzt wird: Zum Bau Ihres Hauses.</div>
    <div class="feat"><svg width="10" height="9" viewBox="0 0 10 9"><path d="M1 5l3 3 5-7" fill="none" stroke="#7cb63f" stroke-width="2"/></svg><h4>Zahlungen nach §3 der Makler- und Bauträgerordnung</h4>Diese gesetzlich geregelte Form der Zahlungsvereinbarung gewährleistet die finanzielle Sicherheit der Kunden der Vorlind Bauunternehmung. Sie schützt Ihr Geld vor missbräuchlicher Verwendung und unberechtigtem Zugriff.</div>
    <div class="feat"><svg width="10" height="9" viewBox="0 0 10 9"><path d="M1 5l3 3 5-7" fill="none" stroke="#7cb63f" stroke-width="2"/></svg><h4>Baubeginn und Bauzeitgarantie</h4>Bei uns erhalten Sie die Garantie für den vereinbarten Baubeginn sowie die Fertigstellung des Objekts. Die Vorlind Bauunternehmung garantiert Ihnen die erforderliche Bauzeit und Sie planen entspannt den zuverlässigen Zeitpunkt für den Umzug in Ihr neues Zuhause.</div>
  </div>
  <div class="abs feat-col c2">
    <div class="feat"><svg width="10" height="9" viewBox="0 0 10 9"><path d="M1 5l3 3 5-7" fill="none" stroke="#7cb63f" stroke-width="2"/></svg><h4>Garantie der Vorlind Bauunternehmung für Bau und Sicherheiten</h4>Kunden von uns haben das Recht auf die maximale und grundsolide Qualität aller Leistungen. Unsere Priorität liegt auf der Termintreue und der qualitativ hochwertigen Durchführung aller erbrachten Arbeiten.</div>
    <div class="feat"><svg width="10" height="9" viewBox="0 0 10 9"><path d="M1 5l3 3 5-7" fill="none" stroke="#7cb63f" stroke-width="2"/></svg><h4>Zertifizierte Architekten kontrollieren als Bauleitung</h4>Die Bauleitung liegt ausschließlich in der Hand zertifizierter Architekten. Diese kontrollieren alle Baufortschritte am Massivbau und arbeiten intensiv mit Bausachverständigen und Handwerkern zusammen.</div>
    <div class="feat"><svg width="10" height="9" viewBox="0 0 10 9"><path d="M1 5l3 3 5-7" fill="none" stroke="#7cb63f" stroke-width="2"/></svg><h4>Schriftliche Baudokumentation in Form eines Bau-Tagebuchs</h4>Jeder Arbeitsschritt wird schriftlich dokumentiert. Diese aufwendige Form eines Bau-Tagebuchs gewährleistet die grundsolide Ausführung aller Arbeiten und die Nachvollziehbarkeit der verwendeten Materialien sowie der entstandenen Kosten. Es ist ein unverzichtbarer Bestandteil des Qualitätsmanagements der Vorlind Bauunternehmung bei jedem Massivbau.</div>
    <div class="feat"><svg width="10" height="9" viewBox="0 0 10 9"><path d="M1 5l3 3 5-7" fill="none" stroke="#7cb63f" stroke-width="2"/></svg><h4>Unabhängige Sachverständige für das Qualitätsmanagement am Bau</h4>Wir arbeiten mit unabhängigen Sachverständigen zusammen. Diese kontrollieren in regelmäßigen Abständen die Qualität der einzelnen Baufortschritte sowie die grundsolide Qualität der Ausführung. So erhalten Sie die Garantie für grundsolide Qualität im Massivbau.</div>
    <div class="feat"><svg width="10" height="9" viewBox="0 0 10 9"><path d="M1 5l3 3 5-7" fill="none" stroke="#7cb63f" stroke-width="2"/></svg><h4>Blow-Door Test</h4>Wohngebäude mit kontrollierter Wohnraumlüftung erfordern den Blow-Door-Test. Dieser Test informiert über die Luft- und Winddichtheit des Massivbau-Gebäudes und ob Ihr neues Eigenheim die vom Gesetzgeber geforderten Werte erzielt.</div>
    <div class="feat"><svg width="10" height="9" viewBox="0 0 10 9"><path d="M1 5l3 3 5-7" fill="none" stroke="#7cb63f" stroke-width="2"/></svg><h4>Energieausweis</h4>Die moderne Zeit bietet beim Massivbau zahlreiche Möglichkeiten der Energieeinsparung und mit gezielten Maßnahmen verwandeln Sie jedes Haus in ein Energiesparhaus. Der Energieausweis nach der Energie-Einsparverordnung (EnEV) bestätigt die leistungsfähige Dämmung und den geringen Energieverbrauch Ihres Hauses.</div>
  </div>
</section>

<!-- Bauberatung -->
<section class="spread s-advice">
  <div class="abs plan-photo" role="img" aria-label="Foto: Grundrissplan mit Taschenrechner, Brille und Stift auf dem Schreibtisch"></div>
  <h2 class="abs h-gold advice-title">Professionelle Bauberatung:<br>Die Garantie für gehobene Qualität</h2>
  <p class="abs advice-text">Für Ihren anstehenden Neubau ist eine fundierte und fachgerechte Bauberatung zu empfehlen. Mit uns als Experten erhalten Sie die Sicherheit, Ihr Objekt im Massivbau nach Ihren expliziten Wohnbedürfnissen umzusetzen und von exakter Anpassung an Ihr Baubudget zu profitieren. Die Vorlind Bauunternehmung bietet Ihnen eine fachkundige Bauberatung mit Garantie, die als Komplettangebot mit Garantie Ihre Bedürfnisse in den Vordergrund stellt und Qualität zum Festpreis bietet.</p>

  <div class="abs step" style="top:36px">
    <svg class="icon" width="52" height="52" viewBox="0 0 52 52" aria-hidden="true"><circle cx="26" cy="26" r="24" fill="none" stroke="#e3ad23" stroke-width="1.5"/><path d="M15 33l18-18 4 4-18 18h-4zM17 17l18 18" fill="none" stroke="#4a4a4a" stroke-width="1.4"/></svg>
    <h3>Die Planung<br>Ihres Bauprojekts mit uns als Fachbetrieb</h3>
    <div class="txt">
      <p>Grundlage unserer fachkundigen Bauplanung ist der Abschluss eines Bauleistungsvertrags zu Festpreisen mit Garantie, für den Sie selbstverständlich ein 14-tägiges Rücktrittsrecht besitzen. Hiernach beginnt unser Architekt als Partner mit der individuellen Objektplanung und erstellt erste Entwürfe, ein Geologe erstellt ein Baugrundgutachten inklusive Gründungsempfehlung.</p>
      <p>Für ein zeitgemäßes Energiekonzept vertrauen wir auf einen Energieberater als Partner, der für Sie ein Wärmekonzept nach Ihren Wünschen entwickelt. In den folgenden Schritten übernehmen unsere Statiker und Architekten die Bauantragsplanung sowie die Erstellung von Werkplan, Statikplan und Entwässerungsplan. Den hierdurch optimal vorbereiteten Bauantrag reichen Sie bei Ihrer Gemeinde ein, die Erteilung der Baugenehmigung erfolgt im Regelfall binnen vier bis sechs Wochen.</p>
    </div>
  </div>

  <div class="abs step" style="top:200px">
    <svg class="icon" width="52" height="52" viewBox="0 0 52 52" aria-hidden="true"><circle cx="26" cy="26" r="24" fill="none" stroke="#e3ad23" stroke-width="1.5"/><rect x="15" y="16" width="22" height="20" fill="none" stroke="#4a4a4a" stroke-width="1.4"/><path d="M15 21h22M20 13v5M32 13v5" stroke="#4a4a4a" stroke-width="1.4"/><circle cx="19" cy="34" r="5" fill="#fff" stroke="#4a4a4a" stroke-width="1.4"/></svg>
    <h3>Die Bauzeit –<br>schnelle Umsetzung für Ihre Zufriedenheit</h3>
    <div class="txt">
      <p>Sobald die Baugenehmigung vorliegt, nehmen unsere Partner-Baufirmen innerhalb von zwei bis drei Monaten die Arbeit auf und sorgen für eine schnelle Umsetzung. Unsere Baupartner übernehmen während der gesamten Bauphase die verschiedenen Gewerke, die Leitung unterliegt unseren Partner-Architekten. Dieser sichert Ihnen zu, alle Aktivitäten rund um Ihren Neubau sachgerecht in einem Bautagebuch zu dokumentieren.</p>
      <p>Die Durchführung verschiedener Bauabschnitte wird durch Gutachter und Sachverständige (PRÜFNORD, BAUKONTROLL) während der Bauphase überprüft und entsprechend für Ihr Bauobjekt zertifiziert. Im Energiebereich führen unsere Berater einen Blow-Door-Test für eine optimale Wärmedämmung Ihres Gebäudes aus. Die Fertigstellung Ihres Baus sichern wir Ihnen abhängig von den Rahmenbedingungen innerhalb von vier bis sechs Monaten nach Baubeginn zu.</p>
    </div>
  </div>

  <div class="abs step" style="top:368px">
    <svg class="icon" width="52" height="52" viewBox="0 0 52 52" aria-hidden="true"><circle cx="26" cy="26" r="24" fill="none" stroke="#e3ad23" stroke-width="1.5"/><circle cx="21" cy="22" r="6" fill="none" stroke="#4a4a4a" stroke-width="1.4"/><path d="M25 26l11 11M31 32l3-3M34 35l3-3" stroke="#4a4a4a" stroke-width="1.4"/></svg>
    <h3>Die Bauübergabe –<br>der grundsolide und seriöse Abschluss</h3>
    <div class="txt">
      <p>Neben unseren Terminvereinbarungen für einzelne Ausbaustufen können Sie Ihren neuen Massivbau gerne auch schlüsselfertig nach kompletter Fertigstellung in Empfang nehmen. Bei Zwischenabnahmen und zum Ende hin werden Protokolle erstellt, mit denen sich jeder einzelne, in adäquater Qualität durchgeführte Schritt nachvollziehen lässt.</p>
      <p>Abschließend erhalten Sie von uns sämtliche Unterlagen wie Baupläne, Zertifikate, Materialnachweise und das Bautagebuch ausgehändigt. Auch den Energieausweis und natürlich Ihre Haustürschlüssel nehmen Sie durch uns in Empfang und profitieren mit Garantie von einem einzigartigen Wohngefühl. Nutzen Sie den direkten Kontakt zu uns, um mehr über die Bauberatung der Vorlind Bauunternehmung zu erfahren und sich persönlich mit unseren Stärken vertraut zu machen.</p>
    </div>
  </div>

  <p class="abs folio" style="left:28px"><b>6</b> / Bauberatung</p>
  <p class="abs folio" style="right:20px">Bauberatung / <b>7</b></p>
</section>

</body>
</html>
```